Need Help having my business card stand out

I am the owner of Birchway Canine Training and would like for my business cards to stand out. I have been trying to keep designing them myself but I can't get what I have in my head on the card. I will try my best to post templates that I like for inspirations. I want something unique but elegant. I don't want in to look cartoony or cheesy. It needs to pop in a pet shop but also in a coffee shop or gym.

Target Market(s)

Dog owners, Married ,No young kids Jr High school kids and up (maybe kids on the way) Executives, Stay at home moms/wives, Small business owners

Industry/Entity Type

Dog Training

Contact Information for Business Card

Lowell Spratt, 281-904-3376, info@birchwaycanine.example, www.birchwaycanine.example

Colors

Designer to choose colors to be used in the design.

Requirements
Must have
• my logo
Should not have
• Cursive lettering

```html
<!DOCTYPE html>
<html lang="en">
<head>
<meta charset="utf-8">
<title>Birchway Canine Training – Business Card</title>
<link href="https://fonts.googleapis.com/css2?family=Roboto:wght@400;500&display=swap" rel="stylesheet">
<style>
  :root {
    --backdrop: #c6c6c8;
    --card-dark: #000000;
    --card-light: #f4f4f4;
    --ink-light: #e6e6e6;
    --ink-white: #ffffff;
    --ink-dark: #2a2a2a;
    --icon-tile: #2b2b2b;
    --icon-glyph: #777777;
  }
  html, body {
    margin: 0;
    padding: 0;
    width: 1200px;
    height: 1200px;
    overflow: hidden;
    background: var(--backdrop);
    font-family: "Roboto", Arial, sans-serif;
  }
  .canvas {
    position: relative;
    width: 1200px;
    height: 1200px;
  }
  .card {
    position: absolute;
    width: 696px;
    height: 399px;
    box-sizing: border-box;
  }
  .card--front {
    left: 249px;
    top: 150px;
    background: var(--card-dark);
  }
  .card--back {
    left: 253px;
    top: 630px;
    background: var(--card-light);
  }

  /* Front: brand mark */
  .brand {
    position: absolute;
    left: 0;
    right: 0;
    text-align: center;
  }
  .brand--front {
    top: 92px;
  }
  .brand__dot {
    display: block;
    margin: 0 auto 14px;
    width: 34px;
    height: 34px;
    border-radius: 50%;
    background: var(--ink-white);
  }
  .brand__name {
    font-weight: 500;
    font-size: 24px;
    letter-spacing: 0.5px;
    color: var(--ink-white);
  }

  .divider {
    position: absolute;
    left: 341px;
    top: 217px;
    width: 2px;
    height: 138px;
    background: var(--ink-white);
  }

  .holder-name {
    position: absolute;
    right: 372px;
    top: 272px;
    margin: 0;
    font-weight: 500;
    font-size: 22px;
    letter-spacing: 0.4px;
    color: var(--ink-light);
    white-space: nowrap;
  }

  .contact {
    position: absolute;
    left: 373px;
    top: 238px;
    margin: 0;
    padding: 0;
    list-style: none;
  }
  .contact__item {
    display: flex;
    align-items: center;
    height: 26px;
    font-size: 18px;
    color: var(--ink-light);
  }
  .contact__item--phone { margin-bottom: 22px; }
  .contact__icon {
    width: 15px;
    height: 15px;
    margin-right: 12px;
    flex: none;
  }

  /* Back */
  .brand--back {
    left: 46px;
    right: auto;
    top: 210px;
    text-align: left;
    display: flex;
    align-items: center;
  }
  .brand--back .brand__dot {
    margin: 0 12px 0 0;
    width: 26px;
    height: 26px;
    background: var(--ink-dark);
  }
  .brand--back .brand__name {
    color: var(--ink-dark);
    font-size: 20px;
  }
  .back-url {
    position: absolute;
    left: 46px;
    top: 332px;
    margin: 0;
    font-size: 19px;
    color: var(--ink-dark);
  }
</style>
</head>
<body>
<div class="canvas">

  <section class="card card--front">
    <div class="brand brand--front">
      <span class="brand__dot"></span>
      <span class="brand__name">Birchway Canine Training</span>
    </div>

    <div class="divider"></div>

    <h1 class="holder-name">LOWELL SPRATT</h1>

    <ul class="contact">
      <li class="contact__item contact__item--phone">
        <svg class="contact__icon" viewBox="0 0 16 16" aria-hidden="true">
          <rect width="16" height="16" fill="var(--icon-tile)"/>
          <path d="M5 3.5l1.6 2.4-1 1c.7 1.4 1.7 2.4 3 3l1-1 2.4 1.6-.8 1.8C7.8 12 4 8.2 3.3 4.3z" fill="var(--icon-glyph)"/>
        </svg>
        281-904-3376
      </li>
      <li class="contact__item">
        <svg class="contact__icon" viewBox="0 0 16 16" aria-hidden="true">
          <rect width="16" height="16" fill="var(--icon-tile)"/>
          <rect x="3" y="4.5" width="10" height="7" fill="none" stroke="var(--icon-glyph)" stroke-width="1.2"/>
          <path d="M3 4.5l5 4 5-4" fill="none" stroke="var(--icon-glyph)" stroke-width="1.2"/>
        </svg>
        info@birchwaycanine.example
      </li>
      <li class="contact__item">
        <svg class="contact__icon" viewBox="0 0 16 16" aria-hidden="true">
          <rect width="16" height="16" fill="var(--icon-tile)"/>
          <circle cx="8" cy="8" r="4.6" fill="none" stroke="var(--icon-glyph)" stroke-width="1.2"/>
          <path d="M3.4 8h9.2M8 3.4c-2 2.6-2 6.6 0 9.2M8 3.4c2 2.6 2 6.6 0 9.2" fill="none" stroke="var(--icon-glyph)" stroke-width="1"/>
        </svg>
        www.birchwaycanine.example
      </li>
    </ul>
  </section>

  <section class="card card--back">
    <div class="brand brand--back">
      <span class="brand__dot"></span>
      <span class="brand__name">Birchway Canine Training</span>
    </div>
    <p class="back-url">www.birchwaycanine.example</p>
  </section>

</div>
</body>
</html>
```